Vibrant, yet professional, stationery set and other designs required.

I need to source a fantastic designer for a new project as part of my company using a new logo designed via sketch harbor.

**UPDATE** I am not looking for just 'fine' design that will suffice. I am looking for something great.

We are a life assurance brokerage based in Dublin, Ireland and BrightRoost.ie is our new website aimed at providing services for young families in Ireland. We are hoping to be the 'Velro' level of service providers in this area and I am looking for the quality of design to reflect this :-) Hopefully that makes sense!

I have a preference for straight lines over curves and waves.

I need...

1. Business card
2. Letterhead
3. Banner (for printing - 76cm X 305cm)
4. Car branding for KORVA 9 (2014 sport model) I believe the templates are freely available online.

Target Market(s)

Parents in Ireland - Aged 27 to 50.

Industry/Entity Type

Financial Planning

Colors

Designer to choose colors to be used in the design.

Requirements
Must have
• All of the items listed in the description above. I like clean, bright, legible, vibrant and professional design.
Should not have
• No silly or 'cheap' looking designs. This is a professional company looking to provide a professional service.

```html
<!DOCTYPE html>
<html lang="en">
<head>
<meta charset="utf-8">
<title>BrightRoost.ie — Business Card</title>
<link rel="stylesheet" href="https://fonts.googleapis.com/css2?family=Open+Sans:wght@400;600&display=swap">
<style>
  :root {
    --backdrop: #eceeef;
    --card-white: #f7f7f6;
    --slate: #7b9098;
    --slate-dark: #5f6f76;
    --sky: #1ea9dc;
    --leaf: #7dc11b;
    --ink: #3c4246;
    --pale: #e9edf4;
    --rule: #c9cdd0;
  }
  * { box-sizing: border-box; margin: 0; padding: 0; }
  html, body { width: 1200px; height: 800px; overflow: hidden; }
  body {
    background: var(--backdrop);
    font-family: "Open Sans", Arial, sans-serif;
    position: relative;
  }
  .card {
    position: absolute;
    top: 250px;
    width: 520px;
    height: 300px;
    border-radius: 3px;
    box-shadow: 0 6px 18px rgba(0,0,0,0.14);
    overflow: hidden;
  }
  .card-front { left: 50px; background: var(--card-white); }
  .card-back { left: 630px; background: var(--slate); }

  .front-brand {
    position: absolute;
    left: 30px; top: 110px; width: 230px;
    display: flex; align-items: center; gap: 10px;
    color: var(--slate-dark);
    font-weight: 600;
    font-size: 28px;
    letter-spacing: -0.3px;
  }
  .brand-dot {
    width: 14px; height: 14px; border-radius: 50%;
    background: var(--slate-dark); flex: none;
  }
  .divider {
    position: absolute;
    left: 272px; top: 36px;
    width: 1px; height: 168px;
    background: var(--rule);
  }
  .details {
    position: absolute;
    left: 290px; top: 34px;
    color: var(--ink);
    font-size: 12.5px;
    line-height: 17px;
  }
  .person-name { color: var(--sky); font-size: 16px; font-weight: 600; line-height: 20px; }
  .person-role { color: var(--leaf); font-size: 15px; line-height: 20px; margin-bottom: 2px; }
  .address { margin-bottom: 8px; }
  .contact-line { display: flex; align-items: center; gap: 8px; }
  .contact-line svg { width: 11px; height: 11px; flex: none; fill: var(--sky); }

  .web-band {
    position: absolute;
    left: 62px; right: 0; top: 224px;
    height: 26px;
    background: var(--leaf);
    color: #fff;
    font-size: 11px;
    letter-spacing: 6px;
    line-height: 26px;
    padding-left: 170px;
  }
  .band-marker {
    position: absolute;
    left: 38px; top: 228px;
    width: 18px; height: 18px;
    background: var(--sky);
  }

  .back-brand {
    position: absolute; inset: 0;
    display: flex; align-items: center; justify-content: center;
    color: var(--pale);
    font-weight: 600;
    font-size: 40px;
  }
</style>
</head>
<body>
  <section class="card card-front">
    <div class="front-brand"><span class="brand-dot"></span>BrightRoost.ie</div>
    <div class="divider"></div>
    <div class="details">
      <p class="person-name">AOIFE KERRIGAN</p>
      <p class="person-role">CEO/FOUNDER</p>
      <p class="address">14 Larchfield Row<br>Ranelagh, Dublin 6</p>
      <p class="contact-line">
        <svg viewBox="0 0 12 12" aria-hidden="true"><path d="M1 4c0-2 2-3 5-3s5 1 5 3l-2 1-1-1.5H4L3 5zM2 6h8l1 5H1z"/></svg>
        601 482 7315
      </p>
      <p class="contact-line">
        <svg viewBox="0 0 12 12" aria-hidden="true"><path d="M3 0h6v12H3zM4 1.5v8h4v-8z"/></svg>
        874 209 5561
      </p>
      <p class="contact-line">
        <svg viewBox="0 0 12 12" aria-hidden="true"><path d="M3 0h6v4H3zM0 4h12v6H9v2H3v-2H0zM4 8v3h4V8z"/></svg>
        455 730 1186
      </p>
      <p class="contact-line">
        <svg viewBox="0 0 12 12" aria-hidden="true"><path d="M0 2h12v8H0zM1 3l5 4 5-4v-.2H1z"/></svg>
        hello@brightroost.ie
      </p>
    </div>
    <span class="band-marker"></span>
    <div class="web-band">www.brightroost.ie</div>
  </section>

  <section class="card card-back">
    <div class="back-brand">BrightRoost.ie</div>
  </section>
</body>
</html>
```